Martial art rank diploma

Need a diploma for a martial arts belt rank . The art is Japanese in origin , traditional is good , stylish , eye catching .
Dragons are good , no cartoon figures . Tacky is not good . Something proud to display
No martial art poses
Must have place for date , head instructor signature

And must say (a blank for students name )
"Having confirmed with all standards and requirements set forth by Brenwick Martial Arts and Fitness , is hereby promoted to the rank of " ( a blank for the rank)
Updates

Reason: nice designs, need to see more to compare

Industry/Entity Type

Martial Art

Requirements
Must have
• Logo attached and name of the school
Nice to have
• Dragon , that does not look like a centipede .

maybe best to have a dragon in the background as a water mark type of thing.
Should not have
• Tacky look or cartoon figures, or any martial art poses

```html
<!DOCTYPE html>
<html lang="en">
<head>
<meta charset="utf-8">
<title>Certificate of Rank – Brenwick Martial Arts and Fitness</title>
<link href="https://fonts.googleapis.com/css2?family=UnifrakturCook:wght@700&family=UnifrakturMaguntia&display=swap" rel="stylesheet">
<style>
  :root {
    --sky-top: #f3c46a;
    --sky-mid: #eeaa48;
    --water: #e4932f;
    --gate-tone: rgba(150, 120, 90, 0.35);
    --title-ink: #4b1616;
    --body-ink: #1b1510;
    --rank-ink: #3c3f44;
    --rule: #1b1510;
    --seal-ring: #5a1414;
    --seal-fill: #7a2020;
    --school-ink: #2b2d33;
  }
  * { margin: 0; padding: 0; box-sizing: border-box; }
  html, body { width: 1200px; height: 848px; overflow: hidden; background: #ffffff; }
  .certificate {
    position: relative;
    width: 1200px;
    height: 848px;
    overflow: hidden;
    font-family: "UnifrakturMaguntia", serif;
    color: var(--body-ink);
  }
  .backdrop {
    position: absolute;
    inset: 0;
    background:
      radial-gradient(ellipse 420px 380px at 600px 380px, rgba(255, 236, 180, 0.55), transparent 70%),
      linear-gradient(180deg, var(--sky-top) 0%, var(--sky-mid) 52%, var(--water) 100%);
  }
  .backdrop-gate {
    position: absolute;
    left: 320px;
    top: 230px;
    width: 560px;
    height: 618px;
    background: linear-gradient(180deg, var(--gate-tone), rgba(150, 120, 90, 0.12));
    border-radius: 6px;
    opacity: 0.55;
  }
  .title {
    position: absolute;
    left: 155px;
    top: 72px;
    width: 750px;
    font-family: "UnifrakturCook", serif;
    font-weight: 700;
    font-size: 86px;
    letter-spacing: -1px;
    line-height: 1;
    color: var(--title-ink);
    text-shadow: 2px 3px 3px rgba(0, 0, 0, 0.45), -1px -1px 0 rgba(255, 220, 200, 0.4);
    white-space: nowrap;
  }
  .seal {
    position: absolute;
    left: 920px;
    top: 20px;
    width: 210px;
    height: 210px;
  }
  .line { position: absolute; white-space: nowrap; line-height: 1; }
  .blank {
    position: absolute;
    height: 0;
    border-top: 2px solid var(--rule);
  }
  .certify { left: 95px; top: 234px; font-size: 54px; }
  .date { top: 338px; font-size: 42px; }
  .statement { left: 55px; font-size: 42px; }
  .rank-label {
    left: 95px;
    top: 572px;
    font-family: "UnifrakturCook", serif;
    font-weight: 700;
    font-size: 74px;
    color: var(--rank-ink);
    text-shadow: 2px 2px 3px rgba(0, 0, 0, 0.45), -1px -1px 0 rgba(255, 255, 255, 0.35);
  }
  .school-name {
    position: absolute;
    left: 48px;
    top: 726px;
    display: flex;
    align-items: center;
    gap: 10px;
    font-family: "UnifrakturMaguntia", serif;
    font-size: 25px;
    color: var(--school-ink);
    white-space: nowrap;
  }
  .school-mark {
    width: 32px;
    height: 32px;
    border-radius: 50%;
    background: var(--seal-fill);
  }
  .signature-role { left: 780px; top: 762px; font-size: 44px; }
</style>
</head>
<body>
  <main class="certificate">
    <div class="backdrop" role="img" aria-label="Photograph of a torii gate standing in water at sunset, in warm orange tones"></div>
    <div class="backdrop-gate" role="img" aria-label="Faint silhouette of the torii gate"></div>

    <h1 class="title">Certificate of A Rank</h1>
    <svg class="seal" viewBox="0 0 210 210" role="img" aria-label="Round seal with a coiled dragon emblem">
      <circle cx="105" cy="105" r="101" fill="#f6dcb0" stroke="var(--seal-ring)" stroke-width="6"/>
      <circle cx="105" cy="105" r="87" fill="var(--seal-fill)" stroke="var(--seal-ring)" stroke-width="4"/>
    </svg>

    <p class="line certify">This is to certify that</p>
    <span class="blank" style="left:588px; top:278px; width:418px;"></span>

    <p class="line date" style="left:102px;">On this</p>
    <span class="blank" style="left:235px; top:374px; width:146px;"></span>
    <p class="line date" style="left:398px;">day of</p>
    <span class="blank" style="left:515px; top:374px; width:150px;"></span>
    <p class="line date" style="left:695px;">in the year of</p>
    <span class="blank" style="left:918px; top:374px; width:180px;"></span>

    <p class="line statement" style="top:418px;">Having confirmed with all standards and requirments&nbsp; set forth</p>
    <p class="line statement" style="top:478px;">by Brenwick Martial Arts and Fitness is here by promoted to</p>

    <p class="line rank-label">The Rank Of</p>
    <span class="blank" style="left:515px; top:634px; width:458px;"></span>

    <div class="school-name">
      <span class="school-mark"></span>
      <span>Brenwick Martial Arts and Fitness</span>
    </div>

    <span class="blank" style="left:775px; top:737px; width:306px;"></span>
    <p class="line signature-role">Head Instructor</p>
  </main>
</body>
</html>
```